BOLD & MINIMALIST DESIGN NEEDED

We want a very bold but minimalistic business card design that is impactful and utilizes both sides of the business card. Our current logo is included for your use.

We want bold fonts and good use of negative space. We don't want the logo to overpower the design.

Target Market(s)

Professionals who are building new commercial buildings.

Industry/Entity Type

Construction

Contact Information for Business Card

Name, Title, email, office phone, cell phone, website

Font styles to use
Serif
Sans Serif

Requirements
Must have
• Bold design!

```html
<!DOCTYPE html>
<html lang="en">
<head>
<meta charset="utf-8">
<title>Crestmont Design + Build — Business Card</title>
<link rel="stylesheet" href="https://fonts.googleapis.com/css2?family=Montserrat:wght@800;900&family=Poppins:wght@400;500;600&display=swap">
<style>
  :root {
    --canvas: #e9e9e6;
    --ink: #111213;
    --paper: #f4f4f3;
    --green: #7dc242;
    --green-light: #c4e27a;
    --green-deep: #5a9b2a;
    --white: #ffffff;
    --rule: #8a8a8a;
  }
  * { margin: 0; padding: 0; box-sizing: border-box; }
  html, body { width: 1200px; height: 917px; overflow: hidden; }
  body {
    background: var(--canvas);
    display: flex;
    align-items: center;
    justify-content: center;
    gap: 90px;
    font-family: "Poppins", sans-serif;
  }
  .card {
    position: relative;
    width: 380px;
    height: 620px;
    border-radius: 24px;
    overflow: hidden;
    box-shadow: 0 14px 30px rgba(0,0,0,0.18);
  }
  .card-front { background: var(--paper); }
  .front-shapes { position: absolute; inset: 0; }
  .brand {
    position: absolute;
    left: 0; right: 0;
    text-align: center;
    font-family: "Montserrat", sans-serif;
    font-weight: 900;
    color: var(--ink);
    line-height: 1.1;
  }
  .brand-mark {
    display: block;
    width: 34px; height: 34px;
    margin: 0 auto 14px;
    border-radius: 50%;
    background: var(--green);
  }
  .front-brand { top: 92px; font-size: 34px; letter-spacing: 1px; }
  .front-brand .brand-sub { font-size: 17px; letter-spacing: 6px; }
  .person {
    position: absolute;
    top: 398px; left: 0; right: 0;
    text-align: center;
  }
  .person-name {
    font-family: "Montserrat", sans-serif;
    font-weight: 900;
    font-size: 30px;
    color: var(--white);
    letter-spacing: 1px;
  }
  .person-title {
    font-size: 15px;
    font-weight: 500;
    color: var(--green);
    letter-spacing: 3px;
    margin-top: 2px;
  }
  .divider {
    position: absolute;
    top: 468px; left: 0; right: 0;
    display: flex;
    align-items: center;
    justify-content: center;
    gap: 8px;
  }
  .divider-line { width: 60px; height: 1px; background: var(--rule); }
  .icon {
    width: 22px; height: 22px;
    border-radius: 50%;
    background: var(--green);
    display: flex; align-items: center; justify-content: center;
  }
  .contact {
    position: absolute;
    top: 500px; left: 0; right: 0;
    text-align: center;
    color: var(--white);
    font-size: 17px;
    line-height: 1.45;
  }
  .website {
    position: absolute;
    bottom: 22px; left: 0; right: 0;
    text-align: center;
    color: var(--ink);
    font-size: 17px;
    font-weight: 500;
  }
  .card-back {
    background: radial-gradient(circle at 60% 45%, var(--green-light) 0%, var(--green) 55%, var(--green-deep) 100%);
  }
  .back-brand { top: 250px; font-size: 36px; letter-spacing: 1px; }
  .back-brand .brand-mark { background: var(--ink); }
  .back-brand .brand-sub { font-size: 18px; letter-spacing: 6px; }
</style>
</head>
<body>
  <section class="card card-front" aria-label="Business card front">
    <svg class="front-shapes" viewBox="0 0 380 620" aria-hidden="true">
      <path d="M0,252 C140,262 300,300 380,360 L380,620 L0,620 Z" fill="var(--green)"/>
      <path d="M0,274 C140,284 300,322 380,384 L380,566 L0,566 Z" fill="var(--ink)"/>
    </svg>
    <div class="brand front-brand">
      <span class="brand-mark"></span>
      CRESTMONT<br><span class="brand-sub">DESIGN + BUILD</span>
    </div>
    <div class="person">
      <div class="person-name">NORA VALE</div>
      <div class="person-title">MANAGER</div>
    </div>
    <div class="divider">
      <span class="divider-line"></span>
      <span class="icon" aria-label="Phone">
        <svg width="12" height="12" viewBox="0 0 24 24"><path d="M6.6 10.8a15 15 0 0 0 6.6 6.6l2.2-2.2a1 1 0 0 1 1-.25 11.4 11.4 0 0 0 3.6.57 1 1 0 0 1 1 1V20a1 1 0 0 1-1 1A17 17 0 0 1 3 4a1 1 0 0 1 1-1h3.5a1 1 0 0 1 1 1c0 1.25.2 2.45.57 3.6a1 1 0 0 1-.25 1z" fill="var(--ink)"/></svg>
      </span>
      <span class="icon" aria-label="Email">
        <svg width="12" height="12" viewBox="0 0 24 24"><rect x="2" y="5" width="20" height="14" rx="2" fill="var(--ink)"/><path d="M3 6l9 7 9-7" stroke="var(--green)" stroke-width="2" fill="none"/></svg>
      </span>
      <span class="divider-line"></span>
    </div>
    <div class="contact">
      <div class="contact-phone">(555) 014-2290</div>
      <div class="contact-email">hello@crestmontbuild.com</div>
    </div>
    <div class="website">www.crestmontbuild.com</div>
  </section>

  <section class="card card-back" aria-label="Business card back">
    <div class="brand back-brand">
      <span class="brand-mark"></span>
      CRESTMONT<br><span class="brand-sub">DESIGN + BUILD</span>
    </div>
  </section>
</body>
</html>
```